Fine Art business needs new website

We need a simple website with a home page, about us page, New sculptures, Sold sculptures, and a contact us page.Our sculptures are very high end one of a kind pieces. As such we need the site to be VERY elegant and professional. Lastly, because I'll be updating pictures on the website on a monthly basis it needs to be user friendly to update (Wordpress is preferred). The only branding we have so far for the business is a business card.
Updates
I wasn't completely ready when this project launched, also I am on the road right now and haven't been able to be as responsive to all you designers as I would like. I will work on giving feedback to all the top designs we've received so far. Thank you all so much for your participation and hardwork.
Target Market(s)
High end customers (affluent), art collectors, interior decorators/designers
Industry/Entity Type
Art Gallery
Coding
Coded - Design and coding required
Number of Pages Required
5+ page
Requirements
Must have
- Easily editable picture gallery for myself so that I can add new pieces(pictures of the pieces), remove sold pieces, etc. I would like the website to be built in wordpress so I can update it. I currently use mangewordpress through Netmarro for my other business website and would like to do the same for this one.
- Pages:
- -Intro page with featured pieces
- -Current pieces gallery (for sale) mainly a picture gallery
- -Sculptures archive (sold pieces) another picture gallery
- -About us: Pull-down of -about the artist (attached content)
- -Artistic Process (attached content)
- -Show Schedule:
- -one page dedicated to "friends of TMV" (basically a link page)
- TO BE CLEAR "www.pineroverslane.com" IS A TOTALLY DIFFERENT SITE AND I'M NOT TRYING TO COMBINE THE TWO OR JOIN THEM INTO ONE. This page needs be more elegant and seperate from the Pine Rovers site.
- UPDATE: I'd like a link to the TMV Faceplume page: https://www.faceplume-social.com/mirelcraftworks/
Nice to have
- I would like the pictures on the gallery pages able to have text connected with them (Materials, price)
- I would like the site style and fonts to be similar to our business cards we've already had designed (picture attached).
Should not have
- Too much flash or other things that will make the site slow to load.

```html
<!DOCTYPE html>
<html lang="en">
<head>
<meta charset="utf-8">
<title>Terra Mica Vault — Fine Art Sculpture</title>
<link rel="stylesheet" href="https://fonts.googleapis.com/css2?family=Cormorant+Garamond:wght@400;500&family=Raleway:wght@400;500;600&display=swap">
<style>
:root{
  --ink:#2b2b2b;
  --text:#555;
  --muted:#888;
  --accent:#c8202a;
  --btn:#4a4a4a;
  --band:#f4f4f4;
  --line:#cfcfcf;
  --footer:#565656;
  --white:#fff;
}
*{box-sizing:border-box;margin:0;padding:0}
html,body{width:1200px;height:4489px;overflow:hidden}
body{position:relative;background:var(--white);font-family:'Raleway',sans-serif;color:var(--text);font-size:14px;line-height:1.45}
.abs{position:absolute}
.serif{font-family:'Cormorant Garamond',serif;color:var(--ink);font-weight:400}
.btn{position:absolute;display:flex;align-items:center;justify-content:center;font-size:13px;background:var(--btn);color:var(--white);border:1px solid var(--btn)}
.btn.outline{background:var(--white);color:var(--ink)}
.section-title{position:absolute;left:0;width:1200px;text-align:center;font-size:38px}
.band{position:absolute;left:0;width:1200px;background:linear-gradient(135deg,#f7f7f7,#efefef 50%,#f7f7f7)}
.pic{position:absolute}
.arrow-pair{position:absolute;display:flex;gap:8px}
.arrow-pair span{width:18px;height:18px;border-radius:50%;border:1px solid #999}
.arrow-pair span.on{background:#555;border-color:#555}

/* header */
.site-header{position:absolute;left:0;top:0;width:1200px;height:90px;z-index:3}
.site-header .logo{position:absolute;top:30px;left:0;width:1200px;text-align:center;font-size:25px;letter-spacing:2px}
/* hero */
.hero-kicker{left:196px;top:286px;font-size:20px}
.hero-title{left:196px;top:300px;font-size:66px;line-height:1}
.hero-text{left:198px;top:378px;width:320px;font-size:14px}
.slider-dot{position:absolute;top:669px;width:9px;height:9px;border-radius:50%;border:1px solid #888}
/* featured */
.tabs{position:absolute;top:1314px;left:0;width:1200px;display:flex;justify-content:center;gap:50px;font-family:'Cormorant Garamond',serif;font-size:20px;color:var(--ink)}
.tabs .active{color:var(--accent)}
.card-name{position:absolute;width:222px;text-align:center;font-size:18px;color:var(--ink)}
.card-price{position:absolute;width:222px;text-align:center;font-size:13px}
/* artists */
.artist-role{font-size:13px;color:var(--ink)}
.artist-name{font-size:25px;white-space:nowrap}
.artist-text{font-size:14px;width:250px}
.link{font-size:13px;text-decoration:underline;color:var(--ink)}
/* process */
.process-list{list-style:none;font-size:13px}
.process-list li{margin-bottom:6px;padding-left:14px;position:relative}
.process-list li::before{content:"";position:absolute;left:0;top:7px;width:5px;height:5px;background:var(--ink);border-radius:50%}
/* schedule */
.event{position:absolute;width:468px;height:150px;border:1px solid var(--line);background:var(--white)}
.event-date{position:absolute;left:26px;top:24px;width:70px;height:98px;background:var(--btn);color:var(--white);font-family:'Cormorant Garamond',serif;text-align:center;font-size:28px;line-height:1.6;border:1px solid #333}
.event-date i{display:block;height:1px;background:var(--white);margin:0 6px}
.event-title{position:absolute;left:114px;top:22px;font-size:21px}
.event-text{position:absolute;left:114px;top:54px;width:320px;font-size:13px;color:var(--text)}
/* footer */
.site-footer{position:absolute;left:0;top:4110px;width:1200px;height:290px;background:var(--footer);color:#eee;font-size:13px}
.site-footer h4{font-family:'Cormorant Garamond',serif;font-weight:500;font-size:17px;color:var(--white);letter-spacing:1px}
.site-footer h4::after{content:"";display:block;width:34px;height:2px;background:#ddd;margin-top:6px}
.site-footer ul{list-style:none}
.site-footer li{margin-bottom:2px}
.field{position:absolute;background:#444;border:1px solid #6a6a6a;color:#bbb;font-size:11px;padding:3px 6px}
.card-badge{width:50px;height:30px;background:#e8e8e8;color:#444;font-size:10px;display:flex;align-items:center;justify-content:center}
.bottom-bar{position:absolute;left:0;top:4400px;width:1200px;height:89px;background:var(--white)}
.social{position:absolute;display:flex;gap:14px;font-size:12px;color:var(--ink);align-items:center}
.social span{display:flex;align-items:center;gap:5px}
.social b{width:12px;height:12px;border-radius:50%;background:#333;display:inline-block}
</style>
</head>
<body>

<!-- Hero -->
<section class="band" style="top:0;height:645px"></section>
<div class="pic" role="img" aria-label="Bronze and stone abstract sculpture on a black plinth" style="left:615px;top:80px;width:440px;height:562px;background:radial-gradient(ellipse closest-side at 50% 45%,#c49a5a,#8a5a2a 50%,#2a221c 85%,rgba(42,34,28,0))"></div>

<header class="site-header">
  <svg class="abs" style="left:84px;top:38px" width="16" height="14" viewBox="0 0 16 14"><rect y="0" width="16" height="2" fill="#333"/><rect y="6" width="16" height="2" fill="#333"/><rect y="12" width="16" height="2" fill="#333"/></svg>
  <div class="logo serif">TERRA MICA VAULT</div>
  <svg class="abs" style="left:1022px;top:36px" width="84" height="18" viewBox="0 0 84 18" fill="none" stroke="#333" stroke-width="1.8">
    <path d="M8 15 L2 8 A3.5 3.5 0 0 1 8 4 A3.5 3.5 0 0 1 14 8 Z"/>
    <path d="M30 3h3l2 9h9l2-6H35"/><circle cx="37" cy="15" r="1.3"/><circle cx="44" cy="15" r="1.3"/>
    <circle cx="71" cy="8" r="5"/><path d="M75 12l5 5"/>
  </svg>
</header>

<div class="abs serif hero-kicker">Art Gallery</div>
<h1 class="abs serif hero-title">Fine Art</h1>
<p class="abs hero-text">Lorem Ipsum is simply dummy text of thematter and typesetting in and industry.</p>
<div class="btn" style="left:200px;top:427px;width:160px;height:40px">Read More</div>
<div class="btn outline" style="left:372px;top:427px;width:160px;height:40px">Shop Now</div>
<svg class="abs" style="left:78px;top:320px" width="26" height="26" viewBox="0 0 26 26"><circle cx="13" cy="13" r="13" fill="#2b2b2b"/><path d="M15 8l-5 5 5 5" stroke="#fff" stroke-width="2" fill="none"/></svg>
<svg class="abs" style="left:1094px;top:320px" width="26" height="26" viewBox="0 0 26 26"><circle cx="13" cy="13" r="13" fill="#2b2b2b"/><path d="M11 8l5 5-5 5" stroke="#fff" stroke-width="2" fill="none"/></svg>
<span class="slider-dot" style="left:570px;background:#555;border-color:#555"></span>
<span class="slider-dot" style="left:586px"></span>
<span class="slider-dot" style="left:602px"></span>
<span class="slider-dot" style="left:618px"></span>

<!-- About -->
<section>
  <div class="pic" role="img" aria-label="Bronze sculpture with spiral shell form on a dark base" style="left:150px;top:770px;width:360px;height:390px;background:radial-gradient(ellipse closest-side at 50% 50%,#b58a4e,#7a532b 50%,#2b231d 85%,rgba(43,35,29,0))"></div>
  <div class="abs serif" style="left:638px;top:826px;font-size:20px">About us</div>
  <h2 class="abs serif" style="left:636px;top:852px;font-size:40px">Who We Are</h2>
  <p class="abs" style="left:638px;top:918px;width:490px;font-size:14px">Lorem Ipsum is simply dummy text of the matter and typesetting in and in the industry Ipsum is simply dummy text of a the matter and a typesetting in and in the industry.</p>
  <div class="btn" style="left:640px;top:1003px;width:162px;height:40px">Read More</div>
</section>

<!-- Featured sculptures -->
<section class="band" style="top:1195px;height:615px"></section>
<h2 class="section-title serif" style="top:1238px">Feature Sculptures</h2>
<nav class="tabs"><span class="active">All</span><span>New Sculptures</span><span>Sold Sculptures</span></nav>
<div class="arrow-pair" style="left:1030px;top:1318px"><span></span><span class="on"></span></div>
<div class="pic" role="img" aria-label="Purple amethyst geode on a gold stand" style="left:120px;top:1382px;width:222px;height:232px;background:radial-gradient(circle at 50% 45%,#6a3a8a,#2a1a30 55%,#111 80%)"></div>
<div class="pic" role="img" aria-label="Dark carved stone sculpture, sold" style="left:365px;top:1382px;width:222px;height:232px;background:radial-gradient(circle at 50% 45%,#5a4030,#1a1410 60%,#0d0d0d)"></div>
<svg class="abs" style="left:365px;top:1382px" width="64" height="64" viewBox="0 0 64 64"><path d="M0 0h64L0 64z" fill="var(--accent)"/><text x="8" y="26" fill="#fff" font-family="Raleway,sans-serif" font-size="15" transform="rotate(-30 20 20)">Sold</text></svg>
<div class="abs" style="left:410px;top:1484px;width:132px;height:40px;border:1px solid #ddd"></div>
<div class="pic" role="img" aria-label="Orange banded geode on a stand" style="left:612px;top:1382px;width:222px;height:232px;background:radial-gradient(circle at 50% 45%,#c8782e,#5a3218 55%,#111 80%)"></div>
<div class="pic" role="img" aria-label="Polished agate slice on a base" style="left:860px;top:1382px;width:222px;height:232px;background:radial-gradient(circle at 50% 45%,#8a5a3a,#3a2418 55%,#111 80%)"></div>
<div class="card-name" style="left:120px;top:1626px">Sculpture Name</div>
<div class="card-name" style="left:365px;top:1626px">Sculpture Name</div>
<div class="card-name" style="left:612px;top:1626px">Sculpture Name</div>
<div class="card-name" style="left:860px;top:1626px">Sculpture Name</div>
<div class="card-price" style="left:120px;top:1655px">$00.00</div>
<div class="card-price" style="left:365px;top:1655px">$00.00</div>
<div class="card-price" style="left:612px;top:1655px">$00.00</div>
<div class="card-price" style="left:860px;top:1655px">$00.00</div>
<div class="btn" style="left:521px;top:1700px;width:158px;height:40px">View All</div>

<!-- Meet the artists -->
<h2 class="section-title serif" style="top:1845px">Meet the Artists</h2>
<p class="abs" style="left:340px;top:1903px;width:520px;text-align:center;font-size:13px">Lorem Ipsum is simply dummy text of the matter and typesetting in a and in the industry.</p>
<div class="pic" role="img" aria-label="Portrait of the sculptor" style="left:120px;top:1985px;width:202px;height:202px;background:linear-gradient(160deg,#8a7a6a,#4a3a30)"></div>
<div class="abs" style="left:345px;top:1988px">
  <div class="artist-role">Bio</div>
  <div class="artist-name serif">Daniel “Rook” Halvorsen</div>
  <p class="artist-text" style="margin-top:8px">Lorem Ipsum is simply dummy text of the matter and typesetting in a and in the industry. Ipsum is simply dummy text of a the matter and a typesetting.</p>
  <div class="link" style="margin-top:8px">Read More</div>
</div>
<div class="pic" role="img" aria-label="Portrait of the artist" style="left:618px;top:1985px;width:202px;height:202px;background:linear-gradient(160deg,#9aa0a8,#5a5048)"></div>
<div class="abs" style="left:838px;top:1988px">
  <div class="artist-role">Bio</div>
  <div class="artist-name serif">Daniel “Rook” Halvorsen</div>
  <p class="artist-text" style="margin-top:8px">Lorem Ipsum is simply dummy text of the matter and typesetting in a and in the industry. Ipsum is simply dummy text of a the matter and a typesetting.</p>
  <div class="link" style="margin-top:8px">Read More</div>
</div>

<!-- Artistic process -->
<section class="band" style="top:2290px;height:610px"></section>
<h2 class="section-title serif" style="top:2330px">Artistic Process</h2>
<h3 class="abs serif" style="left:120px;top:2455px;font-size:24px">Picking out the Rough</h3>
<p class="abs" style="left:120px;top:2508px;width:360px;font-size:13px">The entire artistic process begins with the difficult task of being able to see the potential inside a rough un-finished stone.</p>
<p class="abs" style="left:120px;top:2578px;width:360px;font-size:13px">One would be gobsmacked at the incredible difference between a completely rough specimen and the finished product (see photos below).</p>
<div class="btn" style="left:120px;top:2645px;width:150px;height:38px">View All</div>
<ul class="abs process-list" style="left:120px;top:2698px">
  <li>Shaping the stone</li><li>Polishing the stone</li><li>Balancing and drilling</li><li>Finishing touche</li>
</ul>
<div class="pic" role="img" aria-label="Hand holding a rough split geode" style="left:540px;top:2430px;width:266px;height:360px;background:linear-gradient(160deg,#6a6a55,#3a3828 60%,#2a2a2a)"></div>
<div class="pic" role="img" aria-label="Second half of the rough geode in hand" style="left:813px;top:2430px;width:268px;height:360px;background:linear-gradient(160deg,#7a7460,#4a4430 60%,#303030)"></div>

<!-- Show schedule -->
<h2 class="section-title serif" style="top:2940px">Show Schedule</h2>
<div class="arrow-pair" style="left:1034px;top:2960px"><span></span><span class="on"></span></div>
<article class="event" style="left:120px;top:3020px"><div class="event-date">13<i></i>Oct</div><div class="event-title serif">Fine Art Show</div><p class="event-text">Lorem Ipsum is simply dummy text of the matter and typesetting in a and in the industry.<br><b>Link :</b> www.venuelist.net<br><span class="link">Read More</span></p></article>
<article class="event" style="left:612px;top:3020px"><div class="event-date">13<i></i>Oct</div><div class="event-title serif">Fine Art Show</div><p class="event-text">Lorem Ipsum is simply dummy text of the matter and typesetting in a and in the industry.<br><b>Link :</b> www.venuelist.net<br><span class="link">Read More</span></p></article>
<article class="event" style="left:120px;top:3195px"><div class="event-date">13<i></i>Oct</div><div class="event-title serif">Fine Art Show</div><p class="event-text">Lorem Ipsum is simply dummy text of the matter and typesetting in a and in the industry.<br><b>Link :</b> www.venuelist.net<br><span class="link">Read More</span></p></article>
<article class="event" style="left:612px;top:3195px"><div class="event-date">13<i></i>Oct</div><div class="event-title serif">Fine Art Show</div><p class="event-text">Lorem Ipsum is simply dummy text of the matter and typesetting in a and in the industry.<br><b>Link :</b> www.venuelist.net<br><span class="link">Read More</span></p></article>
<div class="btn" style="left:527px;top:3390px;width:158px;height:40px">View All</div>

<!-- Geode -->
<section class="band" style="top:3510px;height:600px"></section>
<div class="pic" role="img" aria-label="Close view of a crystal-lined geode interior" style="left:120px;top:3592px;width:445px;height:392px;background:radial-gradient(circle at 30% 40%,#3a3430,#8a96a8 40%,#c8d2de 70%,#9aa6b4)"></div>
<div class="abs serif" style="left:600px;top:3640px;font-size:22px">About us</div>
<h2 class="abs serif" style="left:600px;top:3665px;font-size:46px">Geode</h2>
<p class="abs" style="left:600px;top:3726px;width:480px;font-size:13px;line-height:1.35">It is important to remember when talking about Geodes that not all geodes are the same. In fact most geodes from different areas are extremely unique to the area in which they are found. Another interesting fact about Geodes is that the naming of geodes is generally left up to whoever discovers them.</p>
<p class="abs" style="left:600px;top:3818px;width:480px;font-size:13px;line-height:1.35">Which means in some cases the names of certain types of geodes can become skewed when transferring from the miner, to the dealer, to the end consumer.</p>
<div class="btn" style="left:600px;top:3890px;width:160px;height:40px">Read More</div>

<!-- Footer -->
<footer class="site-footer">
  <div class="abs" style="left:120px;top:68px;width:270px">
    <h4>TERRA MICA VAULT</h4>
    <p style="margin-top:18px">Lorem Ipsum is simply dummy text the printing and typesetting industry a the typesetting has be in the industry’s.</p>
    <div style="display:flex;gap:6px;margin-top:10px">
      <div class="card-badge">Veyra</div><div class="card-badge">Meridia</div><div class="card-badge">Dispay</div><div class="card-badge">Amberline</div>
    </div>
  </div>
  <div class="abs" style="left:445px;top:68px">
    <h4>Quick Link</h4>
    <ul style="margin-top:18px"><li>▸ Home</li><li>▸ Sculptures</li><li>▸ Gallery</li><li>▸ Geode</li><li>▸ About us</li><li>▸ Contact</li></ul>
  </div>
  <div class="abs" style="left:632px;top:68px;width:190px">
    <h4>Address</h4>
    <p style="margin-top:18px;padding-left:20px;position:relative"><svg style="position:absolute;left:0;top:3px" width="10" height="14" viewBox="0 0 10 14"><path d="M5 14C5 14 0 8 0 5a5 5 0 0 1 10 0c0 3-5 9-5 9z" fill="#eee"/><circle cx="5" cy="5" r="2" fill="#565656"/></svg>48 Alder Row<br>Brennwick, USA<br>Zip 5521</p>
    <p style="margin-top:8px;padding-left:20px;position:relative"><svg style="position:absolute;left:0;top:3px" width="12" height="12" viewBox="0 0 12 12"><path d="M2 0l3 3-1.5 2a7 7 0 0 0 3.5 3.5L9 7l3 3-2 2C5 12 0 7 0 2z" fill="#eee"/></svg>(555) 014-2290</p>
    <p style="margin-top:8px;padding-left:20px;position:relative"><svg style="position:absolute;left:0;top:4px" width="12" height="9" viewBox="0 0 12 9"><rect width="12" height="9" fill="#eee"/><path d="M0 0l6 5 6-5" stroke="#565656" fill="none"/></svg>hello@pineroverslane.com</p>
  </div>
  <div class="abs" style="left:847px;top:68px">
    <h4>Quick Contact</h4>
  </div>
  <div class="field" style="left:847px;top:122px;width:112px;height:22px">Name</div>
  <div class="field" style="left:965px;top:122px;width:115px;height:22px">Phone</div>
  <div class="field" style="left:847px;top:150px;width:233px;height:58px">Message</div>
  <div class="field" style="left:847px;top:216px;width:60px;height:22px;text-align:center;color:#eee">Send</div>
</footer>
<div class="bottom-bar">
  <p class="abs" style="left:120px;top:34px;font-size:13px;color:var(--ink)">Copyright © 2018 Terra Mica Vault. All Rights Reserved.</p>
  <div class="social" style="left:750px;top:34px">
    <span><b></b>Faceplume</span><span><b></b>Chirpline</span><span><b></b>Snapgrid</span><span><b></b>Talkbridge</span><span><b></b>Reelhaus</span>
  </div>
</div>

</body>
</html>
```